Upscale business cards needed for Board of Directors

We need professional business cards created for members of our family business Board of Directors. We would like these relatively simple and straightforward, but also with a unique element to set them apart. Probably stick with neutral and simple colors - white, grey etc. We need space for the traditional elements, including name, title, address, email/phone number. And we will be creating several from this template so it needs to be template that is easy to switch information in and out of.
Business
See description

```html
<!DOCTYPE html>
<html lang="en">
<head>
<meta charset="utf-8">
<title>Keelstone Holdings – Business Card</title>
<link href="https://fonts.googleapis.com/css2?family=Source+Sans+3:wght@400;600&display=swap" rel="stylesheet">
<style>
  :root {
    --stage: #000000;
    --card-front: #282828;
    --card-back: #b19b6f;
    --ink-light: #f2f2f2;
    --ink-soft: #e4e4e4;
  }
  * { margin: 0; padding: 0; box-sizing: border-box; }
  html, body {
    width: 1200px;
    height: 900px;
    overflow: hidden;
    background: var(--stage);
    font-family: "Source Sans 3", "Myriad Pro", Arial, sans-serif;
  }
  .stage { position: relative; width: 1200px; height: 900px; }
  .card {
    position: absolute;
    top: 200px;
    width: 310px;
    height: 502px;
  }
  .card--front {
    left: 265px;
    background: var(--card-front);
    border-radius: 50px 0 65px 0;
    color: var(--ink-light);
  }
  .card--back {
    left: 641px;
    width: 309px;
    background: var(--card-back);
    border-radius: 0 60px 0 60px;
  }
  .holder {
    position: absolute;
    top: 46px;
    left: 0;
    width: 100%;
    text-align: center;
  }
  .holder__name {
    font-size: 17px;
    font-weight: 600;
    letter-spacing: 0.2px;
    line-height: 20px;
  }
  .holder__title {
    font-size: 14px;
    font-weight: 400;
    line-height: 16px;
  }
  .contact {
    position: absolute;
    top: 114px;
    left: 0;
    width: 100%;
    text-align: center;
    list-style: none;
    font-size: 14px;
    line-height: 17px;
  }
  .company-name {
    position: absolute;
    left: 0;
    width: 100%;
    text-align: center;
    font-size: 27px;
    font-weight: 600;
    line-height: 32px;
  }
  .card--front .company-name { top: 384px; color: var(--ink-soft); }
  .card--back .company-name { top: 412px; color: #ffffff; }
</style>
</head>
<body>
  <main class="stage">
    <section class="card card--front" aria-label="Card front">
      <header class="holder">
        <p class="holder__name">DANIEL MORROW</p>
        <p class="holder__title">Managing Director</p>
      </header>
      <ul class="contact">
        <li>044-512-3368</li>
        <li>d.morrow@keelstone.com</li>
        <li>www.keelstone.com</li>
      </ul>
      <p class="company-name">Keelstone Holdings</p>
    </section>

    <section class="card card--back" aria-label="Card back">
      <p class="company-name">Keelstone Holdings</p>
    </section>
  </main>
</body>
</html>
```